i would like a business card to leave with customers and potential customers for electrical work and for the supply and install of reverse cycle airconditioning in the domestic and commercial market.
I own my own business and im a sole trader. I have an a'class electrical lisence and also a refrigeration lisence so i am
able to offer complete installations in airconditioning by a fully qualified and lisenced tradesman.
im looking for something that comes across as unique and professional.
i had the coluor black and some gold in mind but open to any coluors.
something like Lanterra Electrical & Refrigeration
or Lanterra Air.
i will use this design on a business card to advertise through summer to help generate installs through the busy season.

Target Market(s)

Mainly domestic house holds through summer who are in need of airconditioning and reliable information to acomadate thier cooling and heating requirements

Industry/Entity Type

Electrical

Requirements
Must have
• Business name- Lanterra
My name- Mark Delford
My mobile no- 0438 517 290
My email- mrdelford@qelvo.com.au
Installation & Decomissioning of aiconditioning split systems
LIC NO: TRK 540316
Nice to have
• Lanterra Electrical & Refrigeration

```html
<!DOCTYPE html>
<html lang="en">
<head>
<meta charset="utf-8">
<title>Lanterra Electrical &amp; Refrigeration – Business Card</title>
<link rel="stylesheet" href="https://fonts.googleapis.com/css2?family=Open+Sans:wght@400;600;700&display=swap">
<style>
  :root {
    --page: #e6e7e8;
    --card-light: #4d585d;
    --card-dark: #262e32;
    --band: #2f383c;
    --rule: #b9cccd;
    --glow: #d4e4e3;
    --ink: #ffffff;
    --ink-soft: #e3ecec;
    --chip: #7f9296;
  }
  * { margin: 0; padding: 0; box-sizing: border-box; }
  html, body { width: 1200px; height: 1198px; overflow: hidden; }
  body {
    background: var(--page);
    font-family: "Open Sans", sans-serif;
    color: var(--ink);
    position: relative;
  }
  .card {
    position: absolute;
    overflow: hidden;
    background: linear-gradient(160deg, var(--card-light) 0%, #384247 45%, var(--card-dark) 100%);
  }
  .card svg.sweep { position: absolute; inset: 0; }
  .card-front { left: 80px; top: 138px; width: 705px; height: 439px; }
  .card-back  { left: 411px; top: 611px; width: 709px; height: 447px; }

  .rule {
    position: absolute; left: 0; right: 0; height: 4px;
    background: var(--rule);
  }
  .band {
    position: absolute; left: 0; right: 0; bottom: 0;
    background: var(--band);
  }

  /* front */
  .holder { position: absolute; left: 37px; top: 212px; width: 240px; }
  .holder-name { font-size: 32px; font-weight: 600; line-height: 1; letter-spacing: 0.2px; }
  .holder-role { font-size: 19px; text-align: right; margin-top: 4px; line-height: 1; color: var(--ink-soft); }
  .card-front .rule { top: 355px; }
  .card-front .band { top: 359px; display: flex; align-items: center; justify-content: center; }
  .company { font-size: 27px; font-weight: 700; margin-top: -2px; }

  /* back */
  .contacts {
    position: absolute; left: 439px; top: 156px;
    list-style: none; font-size: 21px; line-height: 31px; color: var(--ink-soft);
  }
  .socials { position: absolute; left: 30px; top: 327px; display: flex; gap: 26px; }
  .social-chip { width: 28px; height: 28px; border-radius: 4px; background: var(--chip); }
  .card-back .rule { top: 366px; }
  .card-back .band { top: 370px; text-align: center; padding-top: 13px; }
  .service { font-size: 17px; line-height: 21px; color: var(--ink-soft); }
</style>
</head>
<body>

<section class="card card-front" aria-label="Card front">
  <svg class="sweep" width="705" height="439" viewBox="0 0 705 439" aria-hidden="true">
    <defs>
      <linearGradient id="frontArc" x1="0" y1="0" x2="1" y2="1">
        <stop offset="0" stop-color="#d4e4e3" stop-opacity="0.15"/>
        <stop offset="0.6" stop-color="#d4e4e3" stop-opacity="0.55"/>
        <stop offset="1" stop-color="#e8f2f1" stop-opacity="0.9"/>
      </linearGradient>
    </defs>
    <path d="M178,0 Q560,50 705,303 L705,250 Q560,40 300,0 Z" fill="url(#frontArc)"/>
    <path d="M178,0 Q560,50 705,303" fill="none" stroke="#eef6f5" stroke-width="2.5" opacity="0.9"/>
  </svg>
  <div class="holder">
    <p class="holder-name">Mark Delford</p>
    <p class="holder-role">CEO</p>
  </div>
  <div class="rule"></div>
  <div class="band"><p class="company">Lanterra Electrical &amp; Refrigeration</p></div>
</section>

<section class="card card-back" aria-label="Card back">
  <svg class="sweep" width="709" height="447" viewBox="0 0 709 447" aria-hidden="true">
    <defs>
      <linearGradient id="backCorner" x1="0" y1="0" x2="0.6" y2="0.8">
        <stop offset="0" stop-color="#a9bcbf"/>
        <stop offset="0.5" stop-color="#6d7f84"/>
        <stop offset="1" stop-color="#4a575c"/>
      </linearGradient>
    </defs>
    <path d="M0,0 L709,0 L709,6 Q200,40 0,318 Z" fill="url(#backCorner)"/>
    <path d="M0,318 Q200,40 709,6" fill="none" stroke="#e6f0ef" stroke-width="3"/>
    <path d="M0,318 Q220,60 709,20" fill="none" stroke="#d4e4e3" stroke-width="10" opacity="0.18"/>
  </svg>
  <ul class="contacts">
    <li>438 517 290</li>
    <li>mrdelford@qelvo.com.au</li>
    <li>lanterra.net/mark</li>
    <li>lanterra.au/mark</li>
    <li>lanterra.au/in/mark</li>
  </ul>
  <div class="socials" aria-hidden="true">
    <span class="social-chip"></span>
    <span class="social-chip"></span>
    <span class="social-chip"></span>
    <span class="social-chip"></span>
  </div>
  <div class="rule"></div>
  <div class="band">
    <p class="service">Installation &amp; Decomissioning of aiconditioning split systems</p>
    <p class="service">LIC NO: TRK 540316</p>
  </div>
</section>

</body>
</html>
```